Redesign of business card for Cedar Ridge Mechanical

We are looking for a new design for our business cards for Cedar Ridge Mechanical. We are a plumbing & HVAC construction company, operating on the West Coast of Canada and USA. Logo attached.
Industry/Entity Type
Construction - Plumbing & HVAC
Contact Information for Business Card
Name, address, phone numbers, email, website address
Look and feel
Each slider illustrates characteristics of the customer's brand and the style your logo design should communicate.

```html
<!DOCTYPE html>
<html lang="en">
<head>
<meta charset="utf-8">
<title>Cedar Ridge Mechanical – Business Cards</title>
<link rel="stylesheet" href="https://fonts.googleapis.com/css2?family=Montserrat:wght@400;700;800&display=swap">
<style>
  :root {
    --ink: #111111;
    --muted: #333333;
    --card: #ffffff;
    --backdrop: #2b2a2c;
    --shadow: rgba(0, 0, 0, 0.45);
  }
  * { box-sizing: border-box; margin: 0; padding: 0; }
  html, body { width: 1200px; height: 913px; overflow: hidden; }
  body {
    background: var(--backdrop);
    font-family: "Montserrat", Arial, sans-serif;
    color: var(--ink);
    position: relative;
  }
  .card {
    position: absolute;
    width: 600px;
    height: 343px;
    background: var(--card);
    border-radius: 22px;
    box-shadow: 0 14px 30px var(--shadow);
    overflow: hidden;
  }
  .card-front { left: 70px; top: 70px; }
  .card-back { left: 530px; top: 500px; }

  .brand {
    display: flex;
    align-items: center;
    gap: 14px;
    font-weight: 800;
    text-transform: uppercase;
    letter-spacing: 0.02em;
    color: var(--ink);
    line-height: 1.05;
  }
  .brand-mark {
    flex: none;
    background: var(--ink);
  }
  .card-front .brand {
    position: absolute;
    left: 50%; top: 50%;
    transform: translate(-50%, -50%);
    font-size: 40px;
    width: 460px;
  }
  .card-front .brand-mark { width: 56px; height: 56px; }

  .card-back .brand-small {
    position: absolute;
    right: 26px; top: 26px;
    font-size: 17px;
    width: 250px;
    gap: 10px;
  }
  .card-back .brand-small .brand-mark { width: 26px; height: 26px; }

  .card-back .brand-large {
    position: absolute;
    left: 60px; bottom: 30px;
    font-size: 34px;
    width: 300px;
  }

  .tab {
    position: absolute;
    left: 0; top: 78px;
    width: 12px; height: 42px;
    background: var(--ink);
  }
  .person {
    position: absolute;
    left: 34px; top: 74px;
  }
  .person-name {
    font-weight: 800;
    font-size: 24px;
    letter-spacing: 0.03em;
    text-transform: uppercase;
  }
  .person-title {
    font-size: 17px;
    color: var(--muted);
    margin-top: 2px;
  }

  .contact {
    position: absolute;
    right: 22px; top: 110px;
    list-style: none;
    text-align: right;
    font-size: 15px;
    line-height: 1.5;
    color: var(--ink);
  }
  .contact li { display: flex; justify-content: flex-end; align-items: center; gap: 8px; }
  .contact .spacer { height: 14px; }
  .contact svg { width: 13px; height: 13px; fill: var(--ink); flex: none; }
  .contact .no-icon { padding-right: 21px; }
</style>
</head>
<body>

<section class="card card-front" aria-label="Business card front">
  <div class="brand"><span class="brand-mark"></span><span>Cedar Ridge Mechanical</span></div>
</section>

<section class="card card-back" aria-label="Business card back">
  <div class="brand brand-small"><span class="brand-mark"></span><span>Cedar Ridge Mechanical</span></div>

  <span class="tab"></span>
  <div class="person">
    <p class="person-name">Daniel Hart</p>
    <p class="person-title">Managing Director</p>
  </div>

  <ul class="contact">
    <li class="no-icon">Your address</li>
    <li>City State, Zip 1234
      <svg viewBox="0 0 24 24" aria-hidden="true"><path d="M12 2a7 7 0 0 0-7 7c0 5 7 13 7 13s7-8 7-13a7 7 0 0 0-7-7zm0 9.5A2.5 2.5 0 1 1 12 6.5a2.5 2.5 0 0 1 0 5z"/></svg></li>
    <li class="spacer"></li>
    <li>123 456 789
      <svg viewBox="0 0 24 24" aria-hidden="true"><path d="M6.6 10.8a15 15 0 0 0 6.6 6.6l2.2-2.2a1 1 0 0 1 1-.25 11.4 11.4 0 0 0 3.6.6 1 1 0 0 1 1 1V20a1 1 0 0 1-1 1A17 17 0 0 1 3 4a1 1 0 0 1 1-1h3.5a1 1 0 0 1 1 1c0 1.25.2 2.45.6 3.6a1 1 0 0 1-.25 1z"/></svg></li>
    <li>info@yourgmail.com
      <svg viewBox="0 0 24 24" aria-hidden="true"><path d="M3 5h18v14H3zm2 2v.5l7 4.5 7-4.5V7z"/></svg></li>
    <li>www.yourwebsite.com
      <svg viewBox="0 0 24 24" aria-hidden="true"><circle cx="12" cy="12" r="10"/></svg></li>
  </ul>

  <div class="brand brand-large"><span>Cedar Ridge Mechanical</span></div>
</section>

</body>
</html>
```